Business Card for a Dental Office

The design should communicate integrity, quality and reliability. We also want the card look elegant, simple, but still stand out, different from the traditional-dental-office business card.

Industry/Entity Type

Business

```html
<!DOCTYPE html>
<html lang="en">
<head>
<meta charset="utf-8">
<title>Harlow Dental Studio – Business Card</title>
<link href="https://fonts.googleapis.com/css2?family=Open+Sans:wght@400;600;700&display=swap" rel="stylesheet">
<style>
  :root {
    --bg: #3a3330;
    --yellow-light: #f3e91f;
    --yellow-dark: #c8b22c;
    --ink: #111111;
    --gold: #c9a227;
    --paper: #ffffff;
    --divider: rgba(0,0,0,0.25);
  }
  * { margin: 0; padding: 0; box-sizing: border-box; }
  html, body {
    width: 1200px; height: 844px; overflow: hidden;
    background: var(--bg);
    font-family: "Open Sans", Arial, sans-serif;
    color: var(--ink);
  }
  .stage {
    position: relative; width: 1200px; height: 844px;
    display: flex; align-items: center; justify-content: center; gap: 60px;
  }
  .card {
    width: 510px; height: 292px; position: relative;
    box-shadow: 0 12px 30px rgba(0,0,0,0.45);
  }
  /* Front */
  .card-front {
    background: linear-gradient(135deg, var(--yellow-light) 0%, var(--yellow-dark) 100%);
    display: flex;
  }
  .brand-panel {
    width: 290px; display: flex; align-items: center; justify-content: center;
    border-right: 1px solid var(--divider);
    margin: 40px 0;
  }
  .brand-name {
    font-weight: 700; font-size: 26px; line-height: 1.15; color: var(--ink);
    text-transform: uppercase; text-align: center;
  }
  .contact-panel {
    flex: 1; padding: 52px 0 0 22px; font-size: 13.5px; line-height: 1.3;
  }
  .person-name { font-weight: 700; font-size: 16px; }
  .person-role { margin-bottom: 14px; }
  .address { margin-bottom: 14px; }
  .contact-list { list-style: none; }
  .contact-list li { display: flex; align-items: center; gap: 8px; }
  .contact-list svg { width: 11px; height: 11px; fill: var(--ink); flex: none; }
  /* Back */
  .card-back {
    background: var(--paper);
    padding: 34px 36px 0 40px;
  }
  .back-brand { margin-left: 90px; }
  .back-brand-name {
    font-weight: 700; font-size: 21px; color: var(--ink); text-transform: uppercase; line-height: 1.1;
  }
  .tagline {
    font-weight: 700; font-size: 10.5px; color: var(--gold); text-transform: uppercase; letter-spacing: 0.3px;
  }
  .appointment-title {
    margin: 16px 0 22px 70px;
    font-weight: 700; font-size: 18px; color: var(--gold);
  }
  .field { display: flex; align-items: baseline; font-size: 14px; margin-bottom: 18px; }
  .field-label { width: 54px; }
  .dots { flex: 1; border-bottom: 2px dotted var(--ink); height: 1px; margin: 0 6px; }
  .notice { font-size: 12.5px; text-align: center; margin-top: 4px; }
</style>
</head>
<body>
<main class="stage">
  <section class="card card-front">
    <div class="brand-panel">
      <p class="brand-name">Harlow<br>Dental Studio</p>
    </div>
    <div class="contact-panel">
      <p class="person-name">Daniel Reeves</p>
      <p class="person-role">Managing Director</p>
      <p class="address">48 Linden Row, Suite 2<br>Eastfield, 204817.</p>
      <ul class="contact-list">
        <li><svg viewBox="0 0 12 12"><path d="M1 4c0-2 2-3 5-3s5 1 5 3l-2 1-1-2H4L3 5zM2 6h8l1 5H1z"/></svg>044-987 654 321</li>
        <li><svg viewBox="0 0 12 12"><path d="M1 2h10v8H1zM1.5 2.5 6 6.5l4.5-4"/></svg>hello@harlowdental.com</li>
        <li><svg viewBox="0 0 12 12"><path d="M5 7 7 5M4 6 2 8a1.5 1.5 0 0 0 2 2l2-2M8 6l2-2a1.5 1.5 0 0 0-2-2L6 4" stroke="#111" stroke-width="1.4" fill="none"/></svg>www.harlowdental.com</li>
      </ul>
    </div>
  </section>

  <section class="card card-back">
    <header class="back-brand">
      <p class="back-brand-name">Harlow Dental Studio</p>
      <p class="tagline">Your smile is your gift to others</p>
    </header>
    <h2 class="appointment-title">Your Next Appointment Is</h2>
    <div class="field"><span class="field-label">Name :</span><span class="dots"></span></div>
    <div class="field"><span class="field-label">Date :</span><span class="dots"></span></div>
    <div class="field"><span class="field-label">Time:</span><span class="dots"></span>AM<span class="dots"></span>PM</div>
    <p class="notice">If unable to keep appointment, kindly give 24hrs notice.</p>
  </section>
</main>
</body>
</html>
```